Brell Stone Company Business Cards

Front and Back Business Card - logo and text setup - cool design. I need workable photoshop or illustrator files so I can setup each employee card with design that is created
Updates

Hi everyone, thank you for the great entries. Please no more white and blue cards - there are so many already - black and silver only now please. thanks!

Target Market(s)

Construction Industry - Facility Managers

Industry/Entity Type

Construction

Contact Information for Business Card

I really like contemporary simplistic looks - clean neat....not opposed to seeing some black backrounds

Requirements
Must have
• Logo/website address with design on front only - www.brellstone-example.com (logo attached)
• Back:
• Name/Title/Company Address/Phone/email address
Nice to have
• Cool design
Should not have
• Nothing gimmicky like Fire or Water - since we are a Fire Protection company - it has all been done

```html
<!DOCTYPE html>
<html lang="en">
<head>
<meta charset="utf-8">
<title>Brell Stone Company – Business Cards</title>
<link href="https://fonts.googleapis.com/css2?family=Arimo:wght@400;700&display=swap" rel="stylesheet">
<style>
  :root {
    --page: #e8e6e3;
    --charcoal: #3d3b3e;
    --charcoal-deep: #393b37;
    --slate-blue: #5a6fad;
    --navy: #2b4a80;
    --amber: #d9901a;
    --white: #ffffff;
    --paper: #f4f4f6;
    --rose: #9a7a86;
    --champagne: #efd9a0;
    --blush: #d8bfc4;
  }
  * { margin: 0; padding: 0; box-sizing: border-box; }
  html, body {
    width: 1200px; height: 1200px; overflow: hidden;
    background: var(--page);
    font-family: "Arimo", Arial, sans-serif;
  }
  .canvas {
    width: 1200px; height: 1200px;
    display: flex; flex-direction: column; align-items: center; justify-content: center;
    gap: 40px;
  }
  .card {
    position: relative;
    width: 945px; height: 540px;
    overflow: hidden;
    background: var(--charcoal);
    box-shadow: 0 6px 18px rgba(0,0,0,.25);
  }
  .card--front { background: var(--charcoal-deep); }
  .card__art { position: absolute; inset: 0; width: 100%; height: 100%; }

  .brand-name {
    position: absolute;
    font-weight: 700;
    color: var(--navy);
    letter-spacing: -0.5px;
    white-space: nowrap;
  }
  .card--back .brand-name {
    left: 44px; top: 78px; font-size: 34px; line-height: 1.1;
  }
  .card--front .brand-name { right: 50px; top: 196px; font-size: 58px; }

  .person {
    position: absolute; right: 40px; top: 138px; text-align: right;
  }
  .person__name {
    color: var(--white); font-weight: 700; font-size: 38px; letter-spacing: 1px;
  }
  .person__title {
    color: var(--amber); font-weight: 700; font-size: 27px; letter-spacing: 1px;
  }
  .address {
    position: absolute; right: 40px; top: 248px; text-align: right;
    color: var(--white); font-weight: 700; font-size: 23px; line-height: 1.35;
  }

  .contact {
    position: absolute; display: flex; flex-direction: column; align-items: center; gap: 22px;
    color: var(--white); font-size: 20px; white-space: nowrap;
  }
  .contact__icon {
    width: 48px; height: 48px; border-radius: 50%; background: var(--white);
    display: flex; align-items: center; justify-content: center;
  }
  .contact--email { left: 150px; top: 418px; }
  .contact--web { left: 430px; top: 378px; }
  .contact--phone { left: 720px; top: 338px; }

  .front-web {
    position: absolute; left: 0; right: 0; top: 440px;
    display: flex; flex-direction: column; align-items: center; gap: 10px;
    color: var(--white); font-size: 21px;
  }
</style>
</head>
<body>
<main class="canvas">

  <section class="card card--back">
    <svg class="card__art" viewBox="0 0 945 540" aria-hidden="true">
      <defs>
        <linearGradient id="metal-back" x1="0" y1="0.5" x2="1" y2="0">
          <stop offset="0" stop-color="var(--rose)"/>
          <stop offset="0.35" stop-color="var(--champagne)"/>
          <stop offset="0.7" stop-color="var(--blush)"/>
          <stop offset="1" stop-color="var(--rose)"/>
        </linearGradient>
        <linearGradient id="edge-shade-back" x1="0.55" y1="0.55" x2="0.4" y2="0.4">
          <stop offset="0" stop-color="#2a2a2c" stop-opacity=".85"/>
          <stop offset="1" stop-color="#2a2a2c" stop-opacity="0"/>
        </linearGradient>
      </defs>
      <polygon points="0,0 440,0 0,420" fill="url(#metal-back)"/>
      <polygon points="380,0 440,0 0,420 0,360" fill="url(#edge-shade-back)"/>
      <polygon points="640,0 945,0 945,70 540,150" fill="var(--slate-blue)"/>
      <polygon points="390,270 945,215 945,345 120,505" fill="var(--slate-blue)"/>
      <line x1="640" y1="1" x2="945" y2="1" stroke="var(--amber)" stroke-width="2"/>
    </svg>

    <div class="brand-name">Brell Stone<br>Company</div>

    <div class="person">
      <div class="person__name">NAME SURNAME</div>
      <div class="person__title">MANAGER</div>
    </div>
    <div class="address">Adress. Street. number<br>City CODE</div>

    <div class="contact contact--email">
      <span class="contact__icon">
        <svg width="26" height="18" viewBox="0 0 26 18"><rect x="1" y="1" width="24" height="16" rx="2" fill="var(--navy)"/><polyline points="2,2 13,10 24,2" fill="none" stroke="#fff" stroke-width="1.6"/></svg>
      </span>
      <span>contact@brellstone-example.com</span>
    </div>
    <div class="contact contact--web">
      <span class="contact__icon">
        <svg width="30" height="30" viewBox="0 0 30 30" fill="none" stroke="var(--navy)" stroke-width="2"><circle cx="15" cy="15" r="12"/><ellipse cx="15" cy="15" rx="5" ry="12"/><line x1="3" y1="15" x2="27" y2="15"/><line x1="5" y1="9" x2="25" y2="9"/><line x1="5" y1="21" x2="25" y2="21"/></svg>
      </span>
      <span>www.brellstone-example.com</span>
    </div>
    <div class="contact contact--phone">
      <span class="contact__icon">
        <svg width="18" height="28" viewBox="0 0 18 28"><rect x="2" y="1" width="14" height="26" rx="3" fill="none" stroke="var(--navy)" stroke-width="2"/><rect x="5" y="5" width="8" height="14" fill="var(--navy)"/><circle cx="9" cy="23" r="1.5" fill="var(--navy)"/></svg>
      </span>
      <span>+33 555 010 200</span>
    </div>
  </section>

  <section class="card card--front">
    <svg class="card__art" viewBox="0 0 945 540" aria-hidden="true">
      <defs>
        <linearGradient id="metal-front" x1="0" y1="0.5" x2="1" y2="0">
          <stop offset="0" stop-color="var(--rose)"/>
          <stop offset="0.3" stop-color="var(--champagne)"/>
          <stop offset="0.7" stop-color="var(--blush)"/>
          <stop offset="1" stop-color="var(--rose)"/>
        </linearGradient>
        <linearGradient id="band-shade" x1="0" y1="0" x2="0.35" y2="0">
          <stop offset="0" stop-color="#555" stop-opacity=".5"/>
          <stop offset="1" stop-color="#555" stop-opacity="0"/>
        </linearGradient>
      </defs>
      <polygon points="0,0 580,0 0,300" fill="url(#metal-front)"/>
      <polygon points="700,0 945,0 945,135 440,135" fill="var(--slate-blue)"/>
      <polygon points="0,235 945,110 945,330 0,330" fill="var(--paper)"/>
      <polygon points="0,235 330,192 0,330" fill="url(#band-shade)"/>
      <polygon points="200,330 945,330 945,440 70,400" fill="var(--slate-blue)"/>
    </svg>

    <div class="brand-name">Brell Stone Company</div>

    <div class="front-web">
      <svg width="34" height="34" viewBox="0 0 30 30" fill="none" stroke="#fff" stroke-width="2"><circle cx="15" cy="15" r="12"/><ellipse cx="15" cy="15" rx="5" ry="12"/><line x1="3" y1="15" x2="27" y2="15"/><line x1="5" y1="9" x2="25" y2="9"/><line x1="5" y1="21" x2="25" y2="21"/></svg>
      <span>www.brellstone-example.com</span>
    </div>
  </section>

</main>
</body>
</html>
```